Dental Practice Website design

Design a new website for Brambleford Dental Practice.
Design should be warm, neutral in colour, with some small amount of bright colour if needed but kept to a minimum. Website should look professional, high end. Home page should be easy to navigate and simple for patients to be able to book online.
Logo in files along with some examples of websites that we like. Please ask if any further info needed.
Menu should have:
About
New Patients
Treatments
Fees
Contact Us

Industry/Entity Type

Dentistry

Number of Pages Required

4 page

Font styles to use
Sans Serif

Colors

Designer to choose colors to be used in the design.

Requirements
Must have
• Ravelle ratings badge, book online button,
Nice to have
• neutral, relaxing colours
Should not have
• harsh, bright colours!

```html
<!DOCTYPE html>
<html lang="en">
<head>
<meta charset="utf-8">
<title>Brambleford Dental Practice</title>
<link href="https://fonts.googleapis.com/css2?family=Urbanist:wght@300;400;500;600;700;800&display=swap" rel="stylesheet">
<style>
:root{
  --ink:#111a1f;
  --dark:#1b2b33;
  --teal:#1f3339;
  --muted:#3c4448;
  --soft-bg:#f6f9fb;
  --team-bg:#f8f8f8;
  --join-a:#d9e2e8;
  --join-b:#cfdae3;
  --white:#ffffff;
  --star:#f2b544;
  --mint:#a9ddd0;
  --link:#4d7c8a;
  --footer-text:#dfe6e9;
}
*{margin:0;padding:0;box-sizing:border-box}
html,body{width:1200px;height:3468px;overflow:hidden}
body{font-family:"Urbanist",sans-serif;color:var(--ink);background:var(--white);position:relative}
.abs{position:absolute}
.btn{position:absolute;background:var(--teal);color:var(--white);border-radius:6px;font-size:16px;font-weight:500;display:flex;align-items:center;justify-content:center}
.photo{position:absolute}

/* header */
.site-header{position:absolute;left:0;top:0;width:1200px;height:97px;background:var(--white)}
.brand{position:absolute;left:110px;top:22px;width:160px;font-size:24px;font-weight:400;line-height:26px;color:#6b7378;letter-spacing:.5px}
.brand small{display:block;font-size:12px;letter-spacing:1.5px;line-height:14px}
.nav a{position:absolute;top:38px;font-size:16px;color:var(--ink);text-decoration:none}
.nav a.active{color:var(--link)}

/* hero */
.hero{position:absolute;left:0;top:97px;width:1200px;height:556px;background:linear-gradient(90deg,#f3f4f5,#eceeef)}
.hero-photo{left:580px;top:0;width:620px;height:556px;background:radial-gradient(ellipse at 60% 45%,#e7c2a8 0%,#c8926f 35%,#7a4a33 60%,#ebecee 85%)}
.hero .eyebrow{left:113px;top:104px;font-size:22px;font-weight:700}
.hero h1{left:108px;top:146px;font-size:55px;font-weight:800;line-height:62px;letter-spacing:.5px}
.rating{left:108px;top:374px;width:217px;height:109px;background:var(--white);box-shadow:0 2px 10px rgba(0,0,0,.1);text-align:center}
.rating .dot{width:14px;height:14px;border-radius:50%;background:#9aa6ad;margin:20px auto 6px}
.rating .stars{color:var(--star);font-size:26px;letter-spacing:3px;line-height:28px}
.rating p{font-size:11px;margin-top:6px}

/* about */
.about{position:absolute;left:0;top:653px;width:1200px;height:606px;background:var(--soft-bg)}
.about-photo{left:112px;top:101px;width:436px;height:353px;border-radius:16px;background:linear-gradient(135deg,#c9d3d8,#e8c9b4 45%,#9fc3e0 80%,#d6e2ea)}
.about .eyebrow{left:617px;top:98px;font-size:21px;font-weight:700}
.about h2{left:617px;top:133px;font-size:41px;font-weight:800;letter-spacing:.3px}
.about h2 span{font-weight:700}
.about p{left:629px;top:193px;width:450px;font-size:15px;line-height:29.2px;color:var(--muted)}

/* join */
.join{position:absolute;left:0;top:1259px;width:1200px;height:779px;background:linear-gradient(180deg,var(--join-a),var(--join-b))}
.join h2{left:0;width:1200px;top:78px;text-align:center;font-size:39px;font-weight:800}
.join p{left:278px;width:644px;top:145px;text-align:center;font-size:14.5px;line-height:25.6px;color:var(--muted)}
.service{position:absolute;top:287px;width:315px}
.service .img{height:288px;border-radius:4px}
.service h3{text-align:center;font-size:19px;font-weight:700;letter-spacing:.5px;margin-top:43px}
.service.featured{background:var(--white);height:376px;border-radius:4px;box-shadow:0 4px 14px rgba(0,0,0,.08)}
.service.featured h3{margin-top:30px;display:flex;align-items:center;justify-content:center;gap:12px}

/* team */
.team{position:absolute;left:0;top:2038px;width:1200px;height:503px;background:var(--team-bg)}
.team h2{left:109px;top:100px;font-size:39px;font-weight:800}
.team p{left:109px;top:168px;width:450px;font-size:15.5px;line-height:25.8px;color:var(--muted)}
.member{position:absolute;top:117px;width:214px}
.member .img{height:200px}
.member h4{font-size:18px;font-weight:600;margin:14px 0 0 0}
.member span{font-size:15px;color:var(--muted)}
.member.card{background:var(--white);height:296px;box-shadow:0 2px 12px rgba(0,0,0,.1)}
.member.card h4,.member.card span{padding-left:22px}
.member.card .badge{position:absolute;right:12px;bottom:22px;width:30px;height:30px;border-radius:50%;background:#1d7fc1}

/* testimonials */
.reviews{position:absolute;left:0;top:2541px;width:1200px;height:557px;background:linear-gradient(180deg,#f5f6f7,#eef0f2)}
.reviews h2{left:0;width:1200px;top:68px;text-align:center;font-size:39px;font-weight:800}
.review{position:absolute;top:161px;width:451px;height:281px;background:var(--white);box-shadow:0 2px 14px rgba(0,0,0,.07)}
.review .quote{position:absolute;left:70px;top:-20px;font-size:80px;font-weight:800;font-style:italic;color:var(--mint);line-height:60px}
.review p{position:absolute;left:34px;top:40px;width:390px;font-size:15.5px;line-height:25.8px;color:var(--muted)}
.review .avatar{position:absolute;left:32px;top:161px;width:106px;height:88px;border-radius:4px}
.review .who{position:absolute;left:182px;top:184px;font-size:16px;color:var(--muted)}
.review .who small{display:block;font-size:13px;margin-top:3px}

/* footer */
.site-footer{position:absolute;left:0;top:3098px;width:1200px;height:370px;background:var(--dark);color:var(--footer-text)}
.foot-brand{left:110px;top:108px;font-size:36px;font-weight:300;line-height:36px;letter-spacing:1px;color:#c9d1d5}
.foot-brand small{display:block;font-size:21px;letter-spacing:2px;line-height:26px}
.site-footer h5{position:absolute;top:92px;font-size:17px;font-weight:700;color:var(--white)}
.site-footer ul{position:absolute;top:124px;list-style:none;font-size:15.5px;line-height:25.6px}
.contact-line{position:absolute;left:883px;font-size:16px;display:flex;align-items:center;gap:14px}
.rule{left:110px;top:305px;width:978px;height:1px;background:#55666e}
.copyright{left:0;width:1200px;top:330px;text-align:center;font-size:15.5px}
</style>
</head>
<body>

<header class="site-header">
  <div class="brand">Brambleford<small>DENTAL PRACTICE</small></div>
  <nav class="nav">
    <a class="active" style="left:335px">Home</a>
    <a style="left:409px">About</a>
    <a style="left:485px">New Patients</a>
    <a style="left:614px">Treatments</a>
    <a style="left:727px">Fees</a>
    <a style="left:790px">Contact Us</a>
  </nav>
  <div class="btn" style="left:936px;top:23px;width:151px;height:51px">Book Online</div>
</header>

<section class="hero">
  <div class="photo hero-photo" role="img" aria-label="Smiling young woman touching her cheek"></div>
  <div class="abs eyebrow">Welcome To</div>
  <h1 class="abs">Our Friendly<br>Dental Practice</h1>
  <div class="btn" style="left:113px;top:283px;width:151px;height:51px">Get Started</div>
  <div class="abs rating">
    <div class="dot"></div>
    <div class="stars">★★★★★</div>
    <p><b>4.9</b> rating from <b>56</b> reviews</p>
  </div>
</section>

<section class="about">
  <div class="photo about-photo" role="img" aria-label="Patient smiling in the dental chair during a check-up"></div>
  <div class="abs eyebrow">About</div>
  <h2 class="abs">Brambleford <span>Dental Practice</span></h2>
  <p class="abs">Welcome to our friendly dental practice nestled in the heart of beautiful Hollowmere, UK. Our team of dedicated dentists, hygienists and support staff are here to provide you with exceptional dental care. With a wide array of services, including general and cosmetic dentistry, orthodontics and emergency care, we're confident that we can deliver the highest quality treatment to you and your loved ones.</p>
  <div class="btn" style="left:617px;top:458px;width:151px;height:51px">Read More</div>
</section>

<section class="join">
  <h2 class="abs">Join Our Practice</h2>
  <p class="abs">If you're looking for an exceptional dental practice, we're here to help! Our team is made up of highly skilled professionals who are dedicated to ensuring that all our patients receive top-notch care in a welcoming and comfortable environment</p>
  <div class="service" style="left:110px">
    <div class="img" role="img" aria-label="Woman smiling during a dental examination" style="background:linear-gradient(135deg,#c5ccd2,#dcb79d 50%,#eef0f2)"></div>
    <h3>General Dentistry</h3>
  </div>
  <div class="service featured" style="left:442px">
    <div class="img" role="img" aria-label="Dentist showing an x-ray to a patient" style="background:linear-gradient(135deg,#eef1f3,#b8c4cc 50%,#4a5e6e)"></div>
    <h3>
      <svg width="34" height="30" viewBox="0 0 34 30" fill="none" stroke="#1b2b33" stroke-width="1.6"><path d="M8 6c3-3 7-2 9 0 2-2 6-3 9 0 3 3 1 9-1 13l-2 8c-1 2-3 1-3-1l-1-6c0-2-3-2-3 0l-1 6c0 2-2 3-3 1l-2-8C7 15 5 9 8 6z"/><path d="M2 26l8-8M4 28l6-6"/></svg>
      Teeth Straightening</h3>
  </div>
  <div class="service" style="left:774px">
    <div class="img" role="img" aria-label="Smiling woman holding a tooth-shaped mirror" style="background:linear-gradient(135deg,#7d8a6a,#d98b5a 40%,#4d8fc6 80%)"></div>
    <h3>Dental Implants</h3>
  </div>
</section>

<section class="team">
  <h2 class="abs">Our Team</h2>
  <p class="abs">We are delighted to introduce you to our experienced and compassionate dental team. Our team comprises highly skilled dental professionals who are dedicated to providing you with high-quality dental care services. Led by our experienced dentist, each member of our team brings their own unique set of skills and expertise.</p>
  <div class="btn" style="left:110px;top:361px;width:151px;height:51px">Read More</div>
  <div class="member card" style="left:630px">
    <div class="img" role="img" aria-label="Portrait of a dentist in a white coat" style="background:linear-gradient(180deg,#dfe4e6,#b99c86 50%,#eceff0)"></div>
    <h4>Dr Mira Castell</h4>
    <span>Dentist</span>
    <div class="badge"></div>
  </div>
  <div class="member" style="left:874px">
    <div class="img" role="img" aria-label="Portrait of the principal dentist in a white coat" style="background:linear-gradient(180deg,#e9edef,#c79f85 45%,#f2f4f5)"></div>
    <h4>Dr Owen Hartley</h4>
    <span>Principal Dentist &amp; Owner</span>
  </div>
</section>

<section class="reviews">
  <h2 class="abs">You Might Also Like</h2>
  <div class="review" style="left:112px">
    <div class="quote">“</div>
    <p>We are passionate about improving dental health and helping you achieve your brightest smile and are honoured that you're considering us for your dental needs. Please don't hesitate to</p>
    <div class="avatar" role="img" aria-label="Customer giving a thumbs up" style="background:linear-gradient(135deg,#2a2522,#c9a27e 55%,#1f1b18)"></div>
    <div class="who">Rosalind<small>Customer</small></div>
  </div>
  <div class="review" style="left:637px">
    <div class="quote">“</div>
    <p>We are passionate about improving dental health and helping you achieve your brightest smile and are honoured that you're considering us for your dental needs. Please don't hesitate to</p>
    <div class="avatar" role="img" aria-label="Smiling customer" style="background:linear-gradient(135deg,#d8e3ea,#d3a98a 55%,#6b4a38)"></div>
    <div class="who">Rosalind<small>Customer</small></div>
  </div>
</section>

<footer class="site-footer">
  <div class="abs foot-brand">Brambleford<small>DENTAL PRACTICE</small></div>
  <h5 style="left:419px">Quick Links</h5>
  <ul style="left:419px"><li>Menu</li><li>About</li><li>New Patients</li><li>Treatments</li><li>Fees</li><li>Contact Us</li></ul>
  <h5 style="left:589px">Opening Hours</h5>
  <ul style="left:589px"><li>Monday</li><li>Tuesday</li><li>Wednesday</li><li>Thursday</li><li>Friday</li><li>Saturday</li></ul>
  <ul style="left:698px"><li>09:00 - 18:00</li><li>09:00 - 20:00</li><li>09:00 - 18:00</li><li>09:00 - 18:00</li><li>09:00 - 17:00</li><li>09:00 - 13:00</li></ul>
  <h5 style="left:883px">Contact</h5>
  <div class="contact-line" style="top:146px">
    <svg width="20" height="20" viewBox="0 0 24 24" fill="#ffffff"><path d="M6.6 10.8a15 15 0 006.6 6.6l2.2-2.2a1 1 0 011-.25 11.4 11.4 0 003.6.57 1 1 0 011 1V20a1 1 0 01-1 1A17 17 0 013 4a1 1 0 011-1h3.5a1 1 0 011 1c0 1.25.2 2.45.57 3.57a1 1 0 01-.25 1z"/></svg>
    020 7946 0321</div>
  <div class="contact-line" style="top:177px">
    <svg width="20" height="16" viewBox="0 0 20 16" fill="none" stroke="#ffffff" stroke-width="1.5"><rect x="1" y="1" width="18" height="14"/><path d="M1 1l9 8 9-8M1 15l7-7M19 15l-7-7"/></svg>
    hello@bramblefordsmiles.co.uk</div>
  <div class="abs rule"></div>
  <div class="abs copyright">Copyright © Brambleford Dental Practice. All rights reserved.</div>
</footer>

</body>
</html>
```